Modern Label for cleaning products for the brand Vorlix

We need a label design for our line of cleaning products. The label should feature our logo and an image to identify the product's intended use. I've added our logo and an image for use. This only concerns the design of the label on the front of the bottle.

Label dimensions:
Label 1 (500ml bottle with spray): width 58mm x height 115mm
Label 2: (1L bottle): width 73mm x height 140mm
The design must be consistent for both bottles which you find in the pictures.

The bottles to be labeled are white. See the attachment for a photo of the bottles.

The photo must also appear on the label to identify the product's intended use.

Product information:
Brand: Vorlix
Product: Sanitary Cleaner

This text must be placed on the label:
"Cleans, descales & freshens. followed with this text: "Ideal for quick and powerful cleaning. A ready-to-use product for everyday use."

- Mention the seperate USP's: Sanitary, Bathroom, Toilet, Wet areas

Appearance: This is a consumer product, but it must have a professional appearance. We would like to see a design that use the color blue from our logo.

Target Market(s)

Consumers who take care of their homes and want to maintain it the correct (professional) way

Font styles to use
Sans Serif

Colors
0054AA
0677BA
7BADD7
CADEEF
E8F1F8

Requirements
Must have
• USP's + use of image and logo + blend in 1 design
Nice to have
• Keep the color of the logo in the design
Should not have
• Comic sans

```html
<!DOCTYPE html>
<html lang="en">
<head>
<meta charset="utf-8">
<title>Vorlix Sanitary Cleaner – Label Set</title>
<link rel="stylesheet" href="https://fonts.googleapis.com/css2?family=Anton&family=Archivo+Black&family=Arimo&family=Poppins:wght@500;600;700&display=swap">
<style>
  :root{
    --ink:#1a1a1a;
    --brand-blue:#0677BA;
    --title-blue:#0a8fd6;
    --band-blue:#0a8bd0;
    --text-blue:#0677BA;
    --shadow-dark:#10202c;
    --lime:#acd121;
    --lime-foot:#d9e687;
    --sky-foot:#a3d9f5;
    --dim-blue:#2a6fa8;
    --white:#ffffff;
  }
  html,body{margin:0;padding:0;width:1200px;height:1200px;overflow:hidden;}
  .board{
    width:1200px;height:1200px;position:relative;
    background:radial-gradient(circle at 50% 50%, #ffffff 0%, #f1f1f1 45%, #d9d9d9 100%);
  }
  .board svg{position:absolute;left:0;top:0;width:1200px;height:1200px;}
  .brand-name{font-family:"Poppins",sans-serif;font-weight:700;fill:var(--ink);}
  .brand-dot{fill:var(--brand-blue);}
  .title-main{font-family:"Anton",sans-serif;fill:var(--title-blue);filter:drop-shadow(6px 4px 0 var(--shadow-dark));}
  .title-sub{font-family:"Archivo Black",sans-serif;fill:var(--title-blue);filter:drop-shadow(5px 4px 0 var(--shadow-dark));}
  .usp{font-family:"Poppins",sans-serif;font-weight:700;fill:var(--text-blue);}
  .tick circle{fill:none;stroke:var(--text-blue);stroke-width:3;}
  .tick path{fill:none;stroke:var(--text-blue);stroke-width:3.5;stroke-linecap:round;stroke-linejoin:round;}
  .tagline{font-family:"Poppins",sans-serif;font-weight:600;fill:var(--text-blue);text-anchor:middle;}
  .footnote{font-family:"Poppins",sans-serif;font-weight:500;fill:var(--text-blue);text-anchor:end;}
  .volume{font-family:"Poppins",sans-serif;font-weight:700;fill:var(--text-blue);}
  .seal-ring{fill:var(--white);stroke:var(--text-blue);stroke-width:4;}
  .seal-core{fill:var(--brand-blue);}
  .dim line{stroke:var(--dim-blue);stroke-width:2.5;}
  .dim polygon{fill:var(--dim-blue);}
  .dim text{font-family:"Arimo",sans-serif;font-size:60px;fill:var(--dim-blue);text-anchor:middle;dominant-baseline:middle;}
</style>
</head>
<body>
<div class="board">
<svg viewBox="0 0 1932 1932" xmlns="http://www.w3.org/2000/svg">
  <defs>
    <linearGradient id="gold" x1="0" y1="0" x2="1" y2="0">
      <stop offset="0" stop-color="#b8862a"/>
      <stop offset="0.45" stop-color="#fff29a"/>
      <stop offset="1" stop-color="#b8862a"/>
    </linearGradient>
    <linearGradient id="paleLime" x1="0" y1="0" x2="0" y2="1">
      <stop offset="0" stop-color="#fbfbee"/>
      <stop offset="0.6" stop-color="#e6efb2"/>
      <stop offset="1" stop-color="#d9e687"/>
    </linearGradient>
    <linearGradient id="paleSky" x1="0" y1="0" x2="0" y2="1">
      <stop offset="0" stop-color="#eef7fd"/>
      <stop offset="0.6" stop-color="#cfe8f8"/>
      <stop offset="1" stop-color="#a3d9f5"/>
    </linearGradient>
    <linearGradient id="bathroomTones" x1="0" y1="0" x2="1" y2="0">
      <stop offset="0" stop-color="#7f8283"/>
      <stop offset="0.35" stop-color="#a9abab"/>
      <stop offset="0.6" stop-color="#eceded"/>
      <stop offset="1" stop-color="#b9bbbc"/>
    </linearGradient>
    <symbol id="tick" viewBox="0 0 30 30">
      <g class="tick"><circle cx="14" cy="16" r="11"/><path d="M8 15 l5 6 l12 -16"/></g>
    </symbol>
  </defs>

  <!-- Brand header -->
  <g class="brand-header">
    <circle class="brand-dot" cx="551" cy="303" r="80"/>
    <text class="brand-name" x="551" y="452" font-size="78" text-anchor="middle">Vorlix</text>
  </g>

  <!-- Label 500 ml -->
  <g class="label label-500" transform="translate(309 797)">
    <rect width="487" height="965" fill="url(#paleLime)"/>
    <polygon points="0,558 487,558 487,808 0,871" fill="url(#bathroomTones)" role="img" aria-label="Photo of a modern bathroom with glass shower, washbasin and tiled bath"/>
    <polygon points="0,871 487,808 487,818 0,881" fill="url(#gold)"/>
    <polygon points="0,881 487,818 487,965 0,965" fill="var(--lime-foot)"/>
    <polygon points="0,0 487,0 487,96 0,168" fill="var(--lime)"/>
    <polygon points="0,168 487,96 487,106 0,178" fill="url(#gold)"/>
    <polygon points="23,0 288,0 288,61 23,85" fill="var(--white)"/>
    <circle class="brand-dot" cx="62" cy="42" r="25"/>
    <text class="brand-name" x="98" y="54" font-size="36">Vorlix</text>

    <text class="title-main" x="26" y="265" font-size="120" textLength="410" lengthAdjust="spacingAndGlyphs" transform="rotate(-6 26 265)">SANITARY</text>
    <text class="title-sub" x="27" y="323" font-size="62" textLength="318" lengthAdjust="spacingAndGlyphs">CLEANER</text>

    <use href="#tick" x="30" y="368" width="26" height="26"/>
    <text class="usp" x="67" y="394" font-size="32">Cleans</text>
    <use href="#tick" x="30" y="401" width="26" height="26"/>
    <text class="usp" x="67" y="427" font-size="32">Descales</text>
    <use href="#tick" x="30" y="434" width="26" height="26"/>
    <text class="usp" x="67" y="461" font-size="32">Freshens</text>

    <circle class="seal-ring" cx="393" cy="398" r="70"/>
    <circle class="seal-core" cx="393" cy="398" r="44"/>

    <text class="tagline" x="243" y="505" font-size="20">Ideal for quick and powerful cleaning.</text>
    <text class="tagline" x="243" y="530" font-size="20">A ready-to-use product for everyday use</text>

    <text class="volume" x="19" y="924" font-size="30">500ml</text>
    <text class="footnote" x="473" y="864" font-size="17">We use 100%</text>
    <text class="footnote" x="473" y="884" font-size="17">certified organic cleaners,</text>
    <text class="footnote" x="473" y="904" font-size="17">ensuring a safe working environment</text>
    <text class="footnote" x="473" y="924" font-size="17">free of harmful chemicals.</text>
  </g>

  <!-- Label 1000 ml -->
  <g class="label label-1000" transform="translate(1082 587)">
    <rect width="613" height="1175" fill="url(#paleSky)"/>
    <polygon points="0,683 613,683 613,993 0,1078" fill="url(#bathroomTones)" role="img" aria-label="Photo of a modern bathroom with glass shower, washbasin and tiled bath"/>
    <polygon points="0,1078 613,993 613,1005 0,1090" fill="url(#gold)"/>
    <polygon points="0,1090 613,1005 613,1175 0,1175" fill="var(--sky-foot)"/>
    <polygon points="0,0 613,0 613,118 0,213" fill="var(--band-blue)"/>
    <polygon points="0,213 613,118 613,130 0,225" fill="url(#gold)"/>
    <polygon points="30,0 363,0 363,90 30,106" fill="var(--white)"/>
    <circle class="brand-dot" cx="80" cy="54" r="32"/>
    <text class="brand-name" x="124" y="66" font-size="44">Vorlix</text>

    <text class="title-main" x="33" y="335" font-size="150" textLength="490" lengthAdjust="spacingAndGlyphs" transform="rotate(-6 33 335)">SANITARY</text>
    <text class="title-sub" x="35" y="405" font-size="78" textLength="376" lengthAdjust="spacingAndGlyphs">CLEANER</text>

    <use href="#tick" x="38" y="446" width="34" height="34"/>
    <text class="usp" x="85" y="476" font-size="42">Cleans</text>
    <use href="#tick" x="38" y="488" width="34" height="34"/>
    <text class="usp" x="85" y="518" font-size="42">Descales</text>
    <use href="#tick" x="38" y="530" width="34" height="34"/>
    <text class="usp" x="85" y="561" font-size="42">Freshens</text>

    <circle class="seal-ring" cx="496" cy="481" r="87"/>
    <circle class="seal-core" cx="496" cy="481" r="55"/>

    <text class="tagline" x="308" y="617" font-size="25">Ideal for quick and powerful cleaning.</text>
    <text class="tagline" x="308" y="647" font-size="25">A ready-to-use product for everyday use</text>

    <text class="volume" x="16" y="1142" font-size="38">1000ml</text>
    <text class="footnote" x="595" y="1066" font-size="22">We use 100%</text>
    <text class="footnote" x="595" y="1091" font-size="22">certified organic cleaners,</text>
    <text class="footnote" x="595" y="1117" font-size="22">ensuring a safe working environment</text>
    <text class="footnote" x="595" y="1143" font-size="22">free of harmful chemicals.</text>
  </g>

  <!-- Dimension lines -->
  <g class="dim dim-500">
    <line x1="309" y1="728" x2="309" y2="778"/>
    <line x1="796" y1="728" x2="796" y2="778"/>
    <line x1="309" y1="751" x2="420" y2="751"/>
    <line x1="686" y1="751" x2="796" y2="751"/>
    <polygon points="311,751 341,743 341,759"/>
    <polygon points="794,751 764,743 764,759"/>
    <text x="553" y="753">58.00 mm</text>

    <line x1="235" y1="797" x2="300" y2="797"/>
    <line x1="235" y1="1762" x2="300" y2="1762"/>
    <line x1="257" y1="797" x2="257" y2="1135"/>
    <line x1="257" y1="1410" x2="257" y2="1762"/>
    <polygon points="257,799 249,829 265,829"/>
    <polygon points="257,1760 249,1730 265,1730"/>
    <text x="257" y="1272" transform="rotate(-90 257 1272)">115.00 mm</text>
  </g>
  <g class="dim dim-1000">
    <line x1="1082" y1="518" x2="1082" y2="570"/>
    <line x1="1695" y1="518" x2="1695" y2="570"/>
    <line x1="1082" y1="541" x2="1255" y2="541"/>
    <line x1="1523" y1="541" x2="1695" y2="541"/>
    <polygon points="1084,541 1114,533 1114,549"/>
    <polygon points="1693,541 1663,533 1663,549"/>
    <text x="1390" y="543">73.00 mm</text>

    <line x1="998" y1="587" x2="1062" y2="587"/>
    <line x1="998" y1="1762" x2="1062" y2="1762"/>
    <line x1="1019" y1="587" x2="1019" y2="1025"/>
    <line x1="1019" y1="1315" x2="1019" y2="1762"/>
    <polygon points="1019,589 1011,619 1027,619"/>
    <polygon points="1019,1760 1011,1730 1027,1730"/>
    <text x="1021" y="1170" transform="rotate(-90 1021 1170)">140.00 mm</text>
  </g>
</svg>
</div>
</body>
</html>
```